Business Card Design Project

We have 2 businesses which help each other.

Brightvale Care (providing nurses to hospitals/nursing homes etc)

and

Brightvale HR (providing nurses to our brightvale care business - but also providing workers for farms, restaurants meatworks etc)

We would like 2 separate business cards - but similar design and feel

Target Market(s)

Managers of nursing homes, hospitals, farms, meatworks, restauants

Industry/Entity Type

Business

Requirements
Must have
• both logos
https://www.filequay-example.com/s/6v4i7j2fzkpw8wx/BrightvaleHR-Logo-Horizontal.ai
https://www.filequay-example.com/s/dr33nlhq82w3z6t/46051_844932_40145_sourcefile.ai

You may edit the layout of Brightvale HR logo

Name
position
mobile
Phone
name@brightvalehr.com.au
brigthvalehr.com.au

Name
position
mobile
phone
name@brightvalecare.net.au
brightvalecare.net.au

```html
<!DOCTYPE html>
<html lang="en">
<head>
<meta charset="utf-8">
<title>Brightvale HR – Business Cards</title>
<link rel="stylesheet" href="https://fonts.googleapis.com/css2?family=Noto+Sans:wght@400;700&display=swap">
<style>
  :root {
    --canvas-bg: #eeeeee;
    --card-blue: #5681b9;
    --card-gloss: rgba(255, 255, 255, 0.92);
    --text-grey: #4a4a4a;
    --brand-blue: #1e4f96;
    --mark-light: #dfe6f1;
    --mark-mid: #9fb6d6;
    --card-shadow: rgba(0, 0, 0, 0.22);
  }

  * { box-sizing: border-box; margin: 0; padding: 0; }

  html, body {
    width: 1200px;
    height: 900px;
    overflow: hidden;
    background: var(--canvas-bg);
    font-family: "Noto Sans", Verdana, sans-serif;
  }

  .sheet {
    position: relative;
    width: 1200px;
    height: 900px;
  }

  .card {
    position: absolute;
    width: 570px;
    height: 322px;
    left: 315px;
    background:
      linear-gradient(205deg, var(--card-gloss) 0%, rgba(255, 255, 255, 0.35) 18%, rgba(255, 255, 255, 0) 34%),
      var(--card-blue);
    box-shadow: 0 4px 10px var(--card-shadow);
    color: var(--text-grey);
  }

  .card--front { top: 100px; }
  .card--back  { top: 478px; }

  /* Front card */
  .brand {
    position: absolute;
    top: 112px;
    left: 0;
    width: 100%;
    display: flex;
    justify-content: center;
    align-items: center;
    gap: 14px;
  }

  .brand__dot {
    width: 62px;
    height: 62px;
    border-radius: 50%;
    background: radial-gradient(circle at 40% 35%, #ffffff 0%, var(--mark-light) 55%, var(--mark-mid) 100%);
  }

  .brand__name {
    font-size: 32px;
    font-weight: 700;
    color: var(--brand-blue);
    letter-spacing: -0.5px;
  }

  .card__website {
    position: absolute;
    top: 222px;
    left: 0;
    width: 100%;
    text-align: center;
    font-size: 24px;
    letter-spacing: 1px;
  }

  /* Back card */
  .card__emblem {
    position: absolute;
    left: 28px;
    top: 58px;
    width: 160px;
    height: 160px;
    border-radius: 50%;
    background: radial-gradient(circle at 40% 35%, #ffffff 0%, var(--mark-light) 50%, var(--mark-mid) 100%);
  }

  .contact {
    position: absolute;
    left: 208px;
    top: 58px;
    list-style: none;
    font-size: 29px;
    line-height: 47px;
    letter-spacing: 0.5px;
  }

  .card__email {
    position: absolute;
    left: 54px;
    top: 250px;
    font-size: 25px;
    letter-spacing: 0.5px;
  }
</style>
</head>
<body>
  <main class="sheet">
    <section class="card card--front" aria-label="Business card front">
      <div class="brand">
        <span class="brand__dot" aria-hidden="true"></span>
        <span class="brand__name">Brightvale HR</span>
      </div>
      <p class="card__website">brigthvalehr.com.au</p>
    </section>

    <section class="card card--back" aria-label="Business card back">
      <div class="card__emblem" role="img" aria-label="Brand emblem area"></div>
      <ul class="contact">
        <li>Name</li>
        <li>Position</li>
        <li>Mobile</li>
        <li>Phone</li>
      </ul>
      <p class="card__email">name@brightvalehr.com.au</p>
    </section>
  </main>
</body>
</html>
```